Spanish Student Needs a Cover for his PhD Dissertation

Hi everyone :) So, I'm a Corneal surgeon currently finishing my PhD, with a dissertation focused on the evaluation of quality of life in patients affected by a disease called Keratoconus. Just so you know, Keratoconus is a condition in which the cornea (the frontal part of the way) gets thin and bulgy and it decreases vision. What I did during my PhD was designing a questionnaire for evaluating quality of life in this kind of patients.
I need to design a hard cover for my dissertation, which is 200 sheets long. I like kind of minimalistic and geometric designs but I am totally open to suggestions. What needs to be in the cover is the name of the dissertation "Diseño, desarrollo y validación de una encuesta para evaluar el compromiso visual y emocional subjetivos en pacientes con Queratocono" and my name, "Iker Zurmendi". The other thing that needs to go there is the logo of my university (Universidad de Montehierro). Aside from that, anything else is up to the designer. It would be important to use the kind of "red" color I am using in the dissertation. I am attaching the frontal page of my dissertation so you know what kind of design and colors I am using.
In the back part, of the cover, there should be this small inscription: "Iker Zurmendi, MD, es un Oftalmólogo Subespecialista en Cirugía Refractiva de la Universidad Tecnológica Cordillerana (Colombia) y la Universidad de Montehierro (España). Actualmente se desempeña como miembro del Departamento de Córnea y Cirugía Refractiva de la Clínica de Oftalmología Miraluz y como director de su propia compañía de emprendimiento médico Silver Heron Surgical". Please leave a space to place my picture; I will have it taken this week so I don't have it right now, you can just leave the blank spot and I will include it later
The size of the pages is standard "letter" size.
Thanks a lot!

Target Market(s)

PhD Scholars

Font styles to use
Serif

Requirements
Must have
• The "red" color I use on my font. It must be formal but "young".
Nice to have
• I like to keep the design clean, kind of "formal with a young" touch so to speak. I really like gray colors, so it would be nice to have broad areas of gray. I love geometrical designs.
I have uploaded a very early version a friend of mine made (it even had a different title); this can be a starting point for you to work on, but I am more than open to suggestions and new ideas.
Should not have
• Please don't use my whole name, Iker Zurmendi is fine. I don't like ALL CAPITALS.

```html
<!DOCTYPE html>
<html lang="es">
<head>
<meta charset="utf-8">
<title>Cubierta de tesis doctoral — Iker Zurmendi</title>
<link rel="stylesheet" href="https://fonts.googleapis.com/css2?family=Playfair+Display+SC:wght@700&family=Libre+Caslon+Text&family=Montserrat:wght@800&family=Roboto:wght@700&display=swap">
<style>
  :root {
    --crimson: #ad1e43;
    --rose: #c35a66;
    --slate: #808080;
    --paper: #ffffff;
    --ink: #1a1a1a;
    --photo-warm: #c88a5c;
    --photo-light: #e8d2cc;
  }
  * { margin: 0; padding: 0; box-sizing: border-box; }
  html, body { width: 1200px; height: 930px; overflow: hidden; background: var(--paper); }
  .spread { position: relative; width: 1200px; height: 930px; }

  .side-label {
    position: absolute;
    font-family: "Libre Caslon Text", serif;
    font-size: 21px;
    color: var(--crimson);
    transform: translateX(-50%);
  }
  .side-label--front { left: 320px; top: 52px; }
  .side-label--back { left: 903px; top: 59px; }

  .cover {
    position: absolute;
    top: 113px;
    width: 534px;
    height: 691px;
    overflow: hidden;
    box-shadow: 8px 10px 12px rgba(0,0,0,0.55);
  }
  .cover--front { left: 54px; background: var(--paper); }
  .cover--back { left: 612px; background: var(--slate); }

  .cover__art { position: absolute; inset: 0; width: 100%; height: 100%; }

  .university {
    position: absolute;
    left: 20px;
    top: 17px;
    width: 145px;
    text-align: center;
  }
  .university__seal {
    width: 56px; height: 56px;
    margin: 0 auto;
    border-radius: 50%;
    background: var(--paper);
    border: 2px solid #555;
  }
  .university__rule { height: 1px; background: #c8c8c8; margin-top: 9px; }
  .university__name {
    font-family: "Roboto", sans-serif;
    font-weight: 700;
    font-size: 10.6px;
    color: var(--paper);
    margin-top: 5px;
    white-space: nowrap;
  }
  .doctoral-school {
    margin: 5px 4px 0;
    height: 34px;
    background: var(--paper);
    display: flex;
    align-items: center;
    justify-content: center;
    font-family: "Roboto", sans-serif;
    font-weight: 700;
    font-size: 8.6px;
    line-height: 1.15;
    color: #4a4a4a;
    padding: 0 6px;
  }

  .thesis-title {
    position: absolute;
    left: 311px;
    top: 215px;
    width: 223px;
    height: 3px;
    background: var(--crimson);
  }
  .thesis-title--bottom { top: 433px; }
  .thesis-title__text {
    position: absolute;
    left: 186px;
    top: 221px;
    width: 340px;
    text-align: center;
    font-family: "Playfair Display SC", serif;
    font-weight: 700;
    font-size: 25px;
    line-height: 29.4px;
    letter-spacing: 0.2px;
    color: var(--ink);
    white-space: nowrap;
  }

  .author-name {
    position: absolute;
    left: 492px;
    top: 451px;
    writing-mode: vertical-rl;
    font-family: "Montserrat", sans-serif;
    font-weight: 800;
    font-size: 27px;
    letter-spacing: 0.5px;
    color: var(--ink);
    white-space: nowrap;
  }

  .author-bio {
    position: absolute;
    left: 92px;
    top: 44px;
    width: 350px;
    text-align: center;
    font-family: "Libre Caslon Text", serif;
    font-size: 15.2px;
    line-height: 18.9px;
    color: var(--paper);
  }
  .author-photo-slot {
    position: absolute;
    left: 150px;
    top: 279px;
    width: 234px;
    height: 314px;
    border-radius: 14px;
    background: var(--paper);
    display: flex;
    align-items: center;
    justify-content: center;
    font-family: "Libre Caslon Text", serif;
    font-size: 15.5px;
    color: var(--ink);
  }
</style>
</head>
<body>
<main class="spread">
  <p class="side-label side-label--front">Front</p>
  <p class="side-label side-label--back">Back</p>

  <section class="cover cover--front">
    <svg class="cover__art" viewBox="0 0 961 1244" preserveAspectRatio="none">
      <defs>
        <linearGradient id="photo-tones" x1="0" y1="0" x2="1" y2="1">
          <stop offset="0" stop-color="var(--photo-warm)"/>
          <stop offset="1" stop-color="var(--photo-light)"/>
        </linearGradient>
      </defs>
      <polygon class="band-slate" points="0,0 600,0 0,541" fill="var(--slate)"/>
      <polygon class="cover-photo" role="img" aria-label="Espacio para fotografía de primer plano de un ojo" points="0,716 153,586 753,1244 0,1244" fill="url(#photo-tones)"/>
      <polygon class="band-crimson" points="600,0 806,0 200,548 860,1244 753,1244 153,586 0,716 0,541" fill="var(--crimson)"/>
      <polygon class="band-rose" points="200,548 213,536 903,1244 860,1244" fill="var(--rose)"/>
    </svg>

    <div class="university">
      <div class="university__seal"></div>
      <div class="university__rule"></div>
      <p class="university__name">Universidad de Montehierro</p>
      <p class="doctoral-school">Escuela de Doctorado Montehierro</p>
    </div>

    <div class="thesis-title"></div>
    <h1 class="thesis-title__text">"Diseño, desarrollo y<br>validación de una<br>encuesta para evaluar<br>el compromiso visual y<br>emocional subjetivos<br>en pacientes con<br>Queratocono"</h1>
    <div class="thesis-title thesis-title--bottom"></div>

    <p class="author-name">Iker Zurmendi</p>
  </section>

  <section class="cover cover--back">
    <p class="author-bio">"Iker Zurmendi, MD, es un Oftalmólogo Subespecialista en Cirugía Refractiva de la Universidad Tecnológica Cordillerana (Colombia) y la Universidad de Montehierro (España). Actualmente se desempeña como miembro del Departamento de Córnea y Cirugía Refractiva de la Clínica de Oftalmología Miraluz y como director de su propia compañía de emprendimiento médico Silver Heron Surgical"</p>
    <div class="author-photo-slot">Author Photo here</div>
  </section>
</main>
</body>
</html>
```